Chorefinch clone for Asia

I am developing a clone for www.chorefinchly.example. It is meant for Asia (i.e. Singapore, Australia, Indonesian, Philippines, Malaysia).

I need a webdesign that functionally look like chorefinch, but localised with pictures of Asian of multi country (rather than latin american looks).

The color, iconography, images can be different, but the functionality must be all be similar to www.chorefinchly.example

I need a mobile UI as well that is for a mobile app, again, similar to that of chorefinch mobile app.

Note that I need the design for the following pages:
1. homepage
2. login page
3. page after login in.
4. search page & results
5. post a task & confirmation page
6. Payment page
7. User Review page.
8. Sign up page.

The webpages are to be in english....

The features must have photos of friendly looking helpers.

Target Market(s)

Asian countries. To serve a mass market, for part time, one off task job.

Requirements
Must have
• Just use Task Helpers for the name of the site for Starters. I have not arrived at a name yet.

```html
<!DOCTYPE html>
<html lang="en">
<head>
<meta charset="utf-8">
<title>Task Helpers</title>
<link href="https://fonts.googleapis.com/css2?family=Arimo:wght@400;700&display=swap" rel="stylesheet">
<style>
:root{
  --sky:#cfe6f7;
  --sky-deep:#8fc3ea;
  --blue:#2b8fd8;
  --blue-dark:#1c6fb3;
  --orange:#f07a12;
  --orange-dark:#d9600a;
  --green:#5aa832;
  --text:#444;
  --muted:#777;
  --line:#d8d8d8;
  --white:#fff;
}
*{box-sizing:border-box;margin:0;padding:0}
html,body{width:781px;height:1200px;overflow:hidden}
body{font-family:"Arimo",Arial,sans-serif;color:var(--text);background:var(--white);position:relative}
.page-top{position:absolute;left:0;top:0;width:781px;height:380px;background:linear-gradient(180deg,var(--sky-deep) 0%,var(--sky) 55%,#fff 100%)}
.util-links{position:absolute;right:22px;top:6px;display:flex;gap:4px}
.util-links a{font-size:10px;color:#333;background:#fff;padding:3px 8px;border:1px solid var(--line);text-decoration:none}
.brand{position:absolute;left:26px;top:18px;display:flex;align-items:center;gap:10px}
.brand-mark{width:34px;height:34px;border-radius:50%;background:var(--orange)}
.brand-name{font-size:26px;font-weight:700;color:#fff;line-height:1}
.brand-tag{font-size:11px;color:#fff;margin-top:3px}
.main-nav{position:absolute;right:22px;top:70px;height:24px;display:flex;background:var(--blue);border-radius:4px 4px 0 0}
.main-nav a{color:#fff;font-size:11px;text-decoration:none;padding:0 14px;line-height:24px;border-right:1px solid rgba(255,255,255,.35)}
.main-nav a:last-child{border-right:0}
.hero{position:absolute;left:22px;top:96px;width:737px;height:276px;border:4px solid #fff;box-shadow:0 2px 6px rgba(0,0,0,.25);display:flex}
.hero-photo{flex:1;background:linear-gradient(135deg,#b98b6a,#e7c8a8 45%,#7a8fa8)}
.service-menu{width:204px;height:268px;background:var(--orange);list-style:none;display:flex;flex-direction:column}
.service-menu li{flex:1;display:flex;align-items:center;padding-left:12px;color:#fff;font-size:12px;font-weight:700;border-bottom:1px solid rgba(255,255,255,.45)}
.service-menu li:last-child{border-bottom:0}
.pitch{position:absolute;top:402px;left:0;width:781px;text-align:center;font-size:17px;font-weight:700;color:var(--orange)}
.signup{position:absolute;top:432px;left:0;width:781px;display:flex;justify-content:center;gap:8px}
.signup .field{width:210px;height:24px;border:1px solid #bbb;border-radius:3px;font-size:11px;color:#999;padding:5px 8px}
.signup .go{height:24px;padding:0 18px;border-radius:3px;background:var(--green);color:#fff;font-size:12px;font-weight:700;line-height:24px}
.features{position:absolute;top:478px;left:22px;width:737px;display:flex;justify-content:space-between}
.feature{width:236px;display:flex;gap:10px}
.feature-icon{width:56px;height:56px;flex:none;border-radius:50%}
.feature h3{font-size:13px;color:var(--orange-dark);font-weight:700;margin-bottom:4px}
.feature p{font-size:8px;color:var(--muted);line-height:1.35}
.read-more{font-size:9px;font-weight:700;color:#333;margin-top:4px;display:block}
.panel{position:absolute;top:596px;border:1px solid var(--line);background:#fafafa}
.panel-head{height:22px;background:var(--blue);color:#fff;font-size:11px;font-weight:700;line-height:22px;padding-left:10px;position:relative}
.about{left:22px;width:505px;height:195px}
.about p{font-size:8.4px;line-height:1.5;color:var(--muted);padding:8px 10px 0}
.blog{left:542px;width:217px;height:195px}
.post{padding:8px 10px 4px;border-bottom:1px solid var(--line)}
.post h4{font-size:10px;color:var(--orange-dark);margin-bottom:3px}
.post p{font-size:8px;color:var(--muted);line-height:1.35}
.post-meta{display:flex;gap:8px;align-items:center;margin-top:5px;font-size:8px}
.post-meta b{background:#fff;border:1px solid var(--line);padding:1px 5px}
.section-title{position:absolute;left:22px;font-size:14px;font-weight:700;color:var(--blue-dark)}
.partners{position:absolute;top:846px;left:22px;width:737px;display:flex;justify-content:space-between;align-items:center}
.partner{height:28px;border-radius:4px;background:#e3e3e3}
.tags{position:absolute;top:940px;left:22px;width:510px;display:flex;justify-content:space-between}
.tags ul{list-style:none}
.tags li{font-size:8.5px;color:#555;line-height:16px;padding-left:9px;position:relative}
.tags li::before{content:"";position:absolute;left:0;top:6px;width:4px;height:4px;background:var(--orange)}
.invite{position:absolute;top:912px;left:548px;width:211px;height:130px;display:flex;gap:8px}
.invite-photo{width:70px;height:118px;border-radius:35px 35px 6px 6px;background:linear-gradient(180deg,#d7b597,#b79a88 40%,#5a7aa6)}
.invite h3{font-size:17px;color:var(--orange);margin-top:16px}
.invite p{font-size:10px;color:#555;margin-top:2px;line-height:1.3}
.invite .btn{display:inline-block;margin-top:8px;background:var(--orange);color:#fff;font-size:10px;font-weight:700;padding:4px 10px;border-radius:3px}
.footer-band{position:absolute;top:1078px;left:0;width:781px;height:62px;background:linear-gradient(180deg,var(--blue),var(--blue-dark));display:flex;align-items:center;justify-content:space-between;padding:0 22px;color:#fff}
.follow{display:flex;align-items:center;gap:8px;font-size:12px}
.social{width:20px;height:20px;border-radius:50%;background:#fff;opacity:.9}
.callout{font-size:12px}
.callout strong{font-size:20px;margin-left:6px}
.footer-links{position:absolute;top:1140px;left:0;width:781px;height:60px;background:#f1f1f1;display:flex;justify-content:space-between;padding:10px 22px;font-size:9px;color:#666}
.footer-links nav{display:flex;gap:12px}
</style>
</head>
<body>
<div class="page-top"></div>

<div class="util-links"><a href="#">Login</a><a href="#">Sign Up</a><a href="#">Help</a></div>

<div class="brand">
  <span class="brand-mark"></span>
  <div><div class="brand-name">Mira Tan</div><div class="brand-tag">Company tagline here</div></div>
</div>

<nav class="main-nav">
  <a href="#">Main</a><a href="#">About Us</a><a href="#">How it Works</a><a href="#">Member</a><a href="#">Contact Us</a>
</nav>

<section class="hero">
  <div class="hero-photo" role="img" aria-label="Group photo of smiling, friendly helpers"></div>
  <ul class="service-menu">
    <li>Delivery</li><li>House Chores</li><li>Shopping</li><li>Office Help</li><li>Handyman</li><li>Moving Help</li><li>Virtual Assistance</li><li>Event Help</li><li>Skilled</li>
  </ul>
</section>

<h2 class="pitch">Get just about anything done by safe, reliable, awesome people.</h2>
<div class="signup"><div class="field">enter e-mail address</div><div class="go">Get Started</div></div>

<section class="features">
  <div class="feature">
    <div class="feature-icon" role="img" aria-label="Illustration of a delivery truck" style="background:radial-gradient(circle,#e05a1a,#8b3a12)"></div>
    <div><h3>Featured Services</h3><p>Our team can help with errands, cleaning and deliveries across the city, booked quickly and done by trusted local helpers.</p><span class="read-more">read more</span></div>
  </div>
  <div class="feature">
    <div class="feature-icon" role="img" aria-label="Illustration of a house" style="background:radial-gradient(circle,#f0a060,#b84a1c)"></div>
    <div><h3>Featured Services</h3><p>Our team can help with errands, cleaning and deliveries across the city, booked quickly and done by trusted local helpers.</p><span class="read-more">read more</span></div>
  </div>
  <div class="feature">
    <div class="feature-icon" role="img" aria-label="Illustration of a pencil and ruler" style="background:radial-gradient(circle,#f4d28a,#b9874a)"></div>
    <div><h3>Featured Services</h3><p>Our team can help with errands, cleaning and deliveries across the city, booked quickly and done by trusted local helpers.</p><span class="read-more">read more</span></div>
  </div>
</section>

<section class="panel about">
  <div class="panel-head">Little About Us</div>
  <p>Our team is a friendly group of helpers who get everyday tasks done for busy people across Asia. From house chores to office help, each helper is screened and rated so you can book with confidence. We keep prices clear and fair, and every task is tracked from posting to completion for your peace of mind.</p>
  <p>We work in Singapore, Malaysia, Indonesia, the Philippines and Australia, with more cities joining soon. Post a task, pick a helper you like, and relax while the work gets done on time.</p>
  <p>Helpers set their own hours, earn extra income and build a reputation with every review they receive from happy customers.</p>
</section>

<section class="panel blog">
  <div class="panel-head">Recent Blog &amp; Post</div>
  <div class="post"><h4>Headline goes here</h4><p>Short notes on new services, helper stories and tips for getting tasks done faster.</p><div class="post-meta"><b>READ MORE</b><span>2 days ago</span></div></div>
  <div class="post"><h4>Headline goes here</h4><p>Short notes on new services, helper stories and tips for getting tasks done faster.</p><div class="post-meta"><b>READ MORE</b><span>2 days ago</span></div></div>
</section>

<h2 class="section-title" style="top:818px">Featured In</h2>
<div class="partners">
  <div class="partner" style="width:90px"></div>
  <div class="partner" style="width:70px"></div>
  <div class="partner" style="width:100px"></div>
  <div class="partner" style="width:80px"></div>
  <div class="partner" style="width:70px"></div>
  <div class="partner" style="width:100px"></div>
</div>

<h2 class="section-title" style="top:914px">Popular Tags</h2>
<div class="tags">
  <ul><li>Sign up / Log in</li><li>How the Helpers Work</li><li>Meet the Helpers</li><li>Become a Helper</li></ul>
  <ul><li>Refer a friend</li><li>Gift cards</li><li>Helpers for Business</li></ul>
  <ul><li>Boston</li><li>New York City</li><li>SF Bay Area</li><li>Inner City Directory</li></ul>
  <ul><li>Boston</li><li>New York City</li><li>SF Bay Area</li><li>Inner City Directory</li></ul>
</div>

<aside class="invite">
  <div class="invite-photo" role="img" aria-label="Photo of a smiling woman"></div>
  <div><h3>Tell a Friend</h3><p>Get 15% off &amp; more<br>Exciting offers</p><span class="btn">invite your friend</span></div>
</aside>

<footer class="footer-band">
  <div class="follow">Follow us with <span class="social"></span><span class="social"></span><span class="social"></span></div>
  <div class="callout">Need Help, Call Us Now <strong>555-010-2468</strong></div>
</footer>
<div class="footer-links">
  <nav><span>About Us</span><span>Team</span><span>Careers</span><span>Press</span><span>Store</span><span>Blog</span><span>FAQ</span><span>Privacy Policy</span><span>Terms of Use</span></nav>
  <span>Copyright &copy; 2012 Company Name</span>
</div>
</body>
</html>
```